Website Design for Videographer

I am looking to update my website - www.brinolvaske.com. I am a wedding videographer who specialises in natural and documentary videography.

The website will be built by my designer using the Wordpress Plinthworx framework.

Requirements;
I want the website to have a clean white look mixed in with video footage.
Needs to be classy. At the moment my website uses a lot of Gold. On the new look I DO NOT want gold.

Need a web and mobile design for the following 12 pages;

* Home page (need to have example videos and text)
* About (this is about me and my service)
* Videos (examples of my work)
* Testimonials
* Packages
* Contact
* Content (this is to show social media content that I am making in a vertical format and advertise this service).
* Blog (index page for blog)
* Blog pages (individual pages for blog content)
* Wedding Venues Index Page (https://brinolvaske.com/north-east-wedding-venues/)
* Individual venue pages (https://brinolvaske.com/north-east-wedding-venues/marlow-tendle-lodge-wedding-videos/) - Needs to show videos, photos, text as is on the current page.
* Venue Tours (https://brinolvaske.com/wedding-venue-tours/)

My current logo is attached however on the website I want to go for a black and white style for it.

Example styles I like however must not be copied.
https://joswelbrant.co.uk/about/
https://oakandripple.co.uk/ (if done in white)
https://tumblemothpictures.co.uk/

Target Market(s)

Couples getting married aged 25-35

Industry/Entity Type

Weddings

Number of Pages Required

5+ page

Font styles to use
Sans Serif

Requirements
Must have
• A classy look, black and white, use videos and photos.
Should not have
• Gold colour

```html
<!DOCTYPE html>
<html lang="en">
<head>
<meta charset="utf-8">
<title>Brin Olvaske Wedding Films</title>
<link rel="stylesheet" href="https://fonts.googleapis.com/css2?family=Roboto:wght@400;500;600;700&display=swap">
<style>
:root{
  --ink:#000;
  --paper:#fff;
  --text:#111;
  --rule:#555;
  --foot-text:#e6e6e6;
}
*{box-sizing:border-box;margin:0;padding:0}
html,body{width:1200px;height:4545px;overflow:hidden;background:var(--paper)}
body{position:relative;font-family:"Roboto",Arial,sans-serif;color:var(--text)}
a{color:inherit;text-decoration:none}
.abs{position:absolute}
.btn{position:absolute;background:var(--ink);color:var(--paper);font-size:13px;font-weight:500;display:flex;align-items:center;justify-content:center;letter-spacing:.2px;text-transform:uppercase}
.brand{position:absolute;font-size:14px;letter-spacing:4px;font-weight:500;display:flex;align-items:center;gap:10px;white-space:nowrap}
.brand .mark{width:14px;height:14px;border:1.5px solid currentColor}
.site-nav{position:absolute;left:357px;top:74px;display:flex;gap:26px;font-size:13px;font-weight:500;text-transform:uppercase}
.site-nav .drop::after{content:"";display:inline-block;width:6px;height:6px;border-right:1.4px solid #000;border-bottom:1.4px solid #000;transform:rotate(45deg);margin-left:10px;position:relative;top:-3px}
.site-nav .gap{margin-left:16px}
.media{position:absolute;overflow:hidden}
.play{position:absolute;width:166px;height:130px;border-radius:12px;background:rgba(255,255,255,.35);left:50%;top:50%;transform:translate(-50%,-50%)}
.play::after{content:"";position:absolute;left:70px;top:42px;border-left:38px solid rgba(255,255,255,.75);border-top:23px solid transparent;border-bottom:23px solid transparent}
.hero-title{position:absolute;left:0;width:1200px;top:568px;text-align:center;color:var(--paper);font-size:48px;font-weight:600}
.hero-sub{position:absolute;left:0;width:1200px;top:648px;text-align:center;color:var(--paper);font-size:15px}
h2{position:absolute;font-weight:600;color:var(--text)}
.lead{position:absolute;font-size:15px;line-height:23px;color:var(--text)}
/* footer */
.site-footer{position:absolute;left:0;top:4090px;width:1200px;height:455px;background:var(--ink);color:var(--foot-text)}
.site-footer .col{position:absolute;font-size:12.5px;line-height:19px;white-space:nowrap}
.site-footer .col b{display:block;font-weight:600;color:#fff;margin-bottom:10px;font-size:12px}
.site-footer .underline{text-decoration:underline}
.footer-links{list-style:none;margin-top:-4px}
.footer-links li{line-height:26.5px;font-size:12.5px}
.venue-links{list-style:none}
.venue-links li{line-height:21px;font-size:11px}
.social{position:absolute;left:55px;top:178px;display:flex;gap:12px}
.social span{width:16px;height:16px;border-radius:50%;background:#fff}
.award-badge{position:absolute;left:454px;top:66px;width:84px;height:105px;background:#8a7a3c}
.footer-rule{position:absolute;left:53px;top:344px;width:1094px;height:1px;background:var(--rule)}
.legal{position:absolute;top:372px;font-size:11px;white-space:nowrap}
.legal a{text-decoration:underline;margin-left:20px}
</style>
</head>
<body>

<header>
  <div class="brand" style="left:53px;top:92px;color:#333"><span class="mark"></span>BRIN OLVASKE</div>
  <nav class="site-nav">
    <a href="#">Brin Galery</a><a href="#">About Brin</a><a href="#">Contact Us</a>
    <a href="#" class="drop">Packages</a><a href="#" class="drop gap">Blog</a>
  </nav>
  <a class="btn" href="#" style="left:1057px;top:62px;width:90px;height:42px">Enquire</a>
</header>

<section class="hero">
  <div class="media" role="img" aria-label="Black and white photo of a groom lifting his laughing bride against a misty hillside" style="left:0;top:183px;width:1200px;height:534px;background:linear-gradient(180deg,#f2f2f2 0%,#bdbdbd 35%,#6f6f6f 60%,#262626 100%)"></div>
  <h1 class="hero-title">Every love story is unique</h1>
  <p class="hero-sub">I am here to tell yours through stunning imagery. Let me preserve your special day with artistry and passion.</p>
</section>

<section class="intro">
  <h2 style="left:53px;top:785px;font-size:39px;line-height:48px">Wedding Day Is The Most<br>Important Day Of Our Life</h2>
  <p class="lead" style="left:634px;top:786px;width:510px">Your wedding film is the best way to keep this day alive forever … a newlywed's gift that keeps giving … an infinite reminder of those special moments and memories because everything about your wedding day belongs to you</p>
  <a class="btn" href="#" style="left:634px;top:895px;width:166px;height:40px">Check Availability</a>
</section>

<section class="gallery">
  <h2 style="left:53px;top:1077px;font-size:39px">Wedding Gallery</h2>
  <p class="lead" style="left:53px;top:1147px">Explore our curated collection of breathtaking moments.</p>
  <a class="btn" href="#" style="left:1033px;top:1103px;width:114px;height:41px">Watch Film</a>

  <div class="media" role="img" aria-label="Bride and groom facing each other at an indoor ceremony" style="left:53px;top:1235px;width:533px;height:533px;background:linear-gradient(135deg,#2a2a2a,#0d0d0d 60%,#3a3a3a)"><span class="play"></span></div>
  <div class="media" role="img" aria-label="Couple embracing on a hilltop" style="left:612px;top:1235px;width:535px;height:355px;background:linear-gradient(180deg,#efefef,#a9a9a9 55%,#555)"><span class="play"></span></div>
  <div class="media" role="img" aria-label="Groom and veiled bride holding each other outdoors" style="left:53px;top:1797px;width:533px;height:353px;background:linear-gradient(135deg,#ddd,#8a8a8a 50%,#e8e8e8)"><span class="play"></span></div>
  <div class="media" role="img" aria-label="Bride in a ballgown getting ready by a window" style="left:612px;top:1617px;width:535px;height:533px;background:linear-gradient(180deg,#9aa2a4,#6d7577 50%,#b9bfc1)"><span class="play"></span></div>
</section>

<section class="feature">
  <div class="media" role="img" aria-label="Couple walking along a coastal path at dusk" style="left:53px;top:2338px;width:1094px;height:728px;background:linear-gradient(180deg,#a9c0c6 0%,#e7e4dc 45%,#7e8c90 62%,#6b6441 80%,#4c4a34 100%)"><span class="play"></span></div>
  <h2 style="left:53px;top:3133px;font-size:47px">Clara Loves Her Wedding Video</h2>
  <p class="lead" style="left:53px;top:3210px;width:1094px;font-size:14.5px;line-height:22px">But the video isn't just for you. Imagine your grandchildren opening that digital file a century from now to learn about the beautiful day that started their family tree. It's more than simply a video; it's a family heritage that will be treasured for decades. How valuable is that? Knowing that the happiest day of your life will live on forever, and that all of your emotions, smiles, and tears will be felt by future generations. When you think about it, it's simply breath taking.</p>
</section>

<section class="about">
  <div class="media" role="img" aria-label="Portrait of the videographer against a pale grey wall" style="left:53px;top:3463px;width:514px;height:533px;background:linear-gradient(180deg,#d9dde2,#c3c8ce 60%,#3a3f46 100%)"></div>
  <p class="abs" style="left:634px;top:3558px;font-size:19px;font-weight:600">By Brin Olvaske</p>
  <h2 style="left:634px;top:3600px;font-size:46px;line-height:55px">Stunning North East<br>Wedding Films</h2>
  <p class="lead" style="left:634px;top:3733px;width:500px;font-size:14.5px;line-height:22.5px">A trusted and acclaimed North East wedding videographer who has more than 25 years of videography experience.<br>From beautiful barns and luxurious country hotels to sun-drenched Greek Islands and ancient Italian abbeys, he has filmed all kinds of unforgettable weddings.</p>
  <a class="btn" href="#" style="left:634px;top:3864px;width:114px;height:40px">Contact Us</a>
</section>

<footer class="site-footer">
  <div class="brand" style="left:67px;top:113px;color:#fff;font-size:13px"><span class="mark"></span>BRIN OLVASKE</div>
  <div class="social" aria-label="Social links"><span></span><span></span><span></span><span></span><span></span></div>

  <div class="col" style="left:274px;top:67px">
    <b>Contact:</b>
    <a href="#" class="underline">07700 900 318</a><br>
    <a href="#" class="underline">films@brinolvaske.com</a>
  </div>

  <div class="award-badge" role="img" aria-label="Award badge"></div>

  <div class="col" style="left:558px;top:67px">
    <b>Achievment</b>
    Vowline Wedding<br>Awards 2024 Winner
  </div>

  <div class="col" style="left:713px;top:67px">
    <b>Links</b>
    <ul class="footer-links">
      <li>FAQ Section</li><li>North East Wedding Venues</li><li>Commercial Videography</li><li>Free Speeches Guide</li><li>Blog</li><li>Ios Island Weddings</li><li>Lake District Wedding Videos</li>
    </ul>
  </div>

  <div class="col" style="left:932px;top:92px">
    <ul class="venue-links">
      <li>North East Wedding Venues</li><li>Newcastle Wedding Videographer</li><li>Newcastle Wedding Videographer</li><li>Northumberland Wedding Video</li><li>North Yokshire Weddings</li><li>Wedding Venue Tours</li><li>Durham Wedding Videographer</li>
    </ul>
  </div>

  <div class="footer-rule"></div>
  <p class="legal" style="left:53px">© 2024 Fernlake. All rights reserved.</p>
  <p class="legal" style="right:53px"><a href="#">Privacy Policy</a><a href="#">Terms of Service</a><a href="#">Cookies Settings</a></p>
</footer>

</body>
</html>
```